Envelope Design Project

I will need two envelopes to be designed:-

DL size
C4 size

Please see uploaded documents for Design specs:

1) Design specs provided by printer (doc called DL Envelope Specs)
2) Design specs to comply with Kestrel Courier requirements (doc called Kestrel Courier Envelope Design Requirements)

Please adhere to the above for final design. Many thanks.

Target Market(s)

Real Estate Agents, Strata Managers, Builders, Architects, Business Owners

Industry/Entity Type

Printer

Requirements
Must have
• In top left corner
- Logo
- Return address - Suite 6, 19 Marlowe St, Harwick, NSW 2199

```html
<!DOCTYPE html>
<html lang="en">
<head>
<meta charset="utf-8">
<title>Corvane Asbestos &amp; Safety – Envelopes</title>
<link rel="stylesheet" href="https://fonts.googleapis.com/css2?family=Questrial&family=Didact+Gothic&display=swap">
<style>
  :root {
    --bg: #3b3b3b;
    --paper: #ffffff;
    --green: #9dc93b;
    --ink: #1f1f1f;
    --line: #8a8a8a;
  }
  * { margin: 0; padding: 0; box-sizing: border-box; }
  html, body { width: 1200px; height: 900px; overflow: hidden; }
  body { background: var(--bg); position: relative; font-family: "Questrial", sans-serif; }

  .envelope { position: absolute; background: var(--paper); overflow: hidden; }

  .dl-back  { left: 147px; top: 58px;  width: 426px; height: 224px; }
  .dl-front { left: 70px;  top: 148px; width: 430px; height: 214px; }
  .c4-back  { left: 474px; top: 384px; width: 631px; height: 446px; }
  .c4-front { left: 361px; top: 424px; width: 630px; height: 444px; }

  .flap { position: absolute; background: var(--green); }
  .dl-back .flap { left: 0; top: 0; width: 100%; height: 74px; border-radius: 0 0 48px 48px; }
  .c4-back .flap { right: 0; top: 0; width: 78px; height: 100%; border-radius: 66px 0 0 66px; }

  .brand { position: absolute; display: flex; flex-direction: column; }
  .brand-name { color: var(--green); font-family: "Questrial", sans-serif; line-height: 1; letter-spacing: -0.3px; }
  .brand-tagline { font-family: "Didact Gothic", sans-serif; color: var(--ink); font-weight: 700; letter-spacing: 0.2px; white-space: nowrap; }

  .dl-front .brand { left: 20px; top: 22px; }
  .dl-front .brand-name { font-size: 22px; }
  .dl-front .brand-tagline { font-size: 6.5px; margin-top: 2px; }

  .c4-front .brand { left: 27px; top: 32px; }
  .c4-front .brand-name { font-size: 34px; }
  .c4-front .brand-tagline { font-size: 10px; margin-top: 3px; }

  .swoosh { position: absolute; left: 0; bottom: 0; width: 100%; display: block; }

  .return-address { position: absolute; color: var(--ink); font-family: "Didact Gothic", sans-serif; white-space: nowrap; }
  .dl-front .return-address { right: 16px; bottom: 5px; font-size: 7px; }
  .c4-front .return-address { right: 40px; bottom: 8px; font-size: 10px; }
</style>
</head>
<body>

  <div class="envelope dl-back"><div class="flap"></div></div>

  <div class="envelope dl-front">
    <div class="brand">
      <span class="brand-name">Corvane</span>
      <span class="brand-tagline">ASBESTOS &amp; SAFETY</span>
    </div>
    <svg class="swoosh" viewBox="0 0 430 42" height="42" preserveAspectRatio="none" aria-hidden="true">
      <path d="M0 8 C150 14 300 0 430 4" fill="none" stroke="var(--line)" stroke-width="0.6"/>
      <path d="M0 14 C140 22 300 4 430 2" fill="none" stroke="var(--ink)" stroke-width="0.6"/>
      <path d="M0 22 C120 34 280 22 430 6 C280 26 120 40 0 31 Z" fill="var(--ink)"/>
      <path d="M0 34 C140 40 300 24 430 8 L430 42 L0 42 Z" fill="var(--green)"/>
    </svg>
    <span class="return-address">Suite 6, 19 Marlowe St, Harwick, NSW 2199</span>
  </div>

  <div class="envelope c4-back"><div class="flap"></div></div>

  <div class="envelope c4-front">
    <div class="brand">
      <span class="brand-name">Corvane</span>
      <span class="brand-tagline">ASBESTOS &amp; SAFETY</span>
    </div>
    <svg class="swoosh" viewBox="0 0 630 60" height="60" preserveAspectRatio="none" aria-hidden="true">
      <path d="M0 10 C220 20 440 0 630 6" fill="none" stroke="var(--line)" stroke-width="0.8"/>
      <path d="M0 18 C200 32 440 6 630 3" fill="none" stroke="var(--ink)" stroke-width="0.8"/>
      <path d="M0 28 C180 48 420 28 630 8 C420 34 180 56 0 40 Z" fill="var(--ink)"/>
      <path d="M0 48 C200 56 440 34 630 11 L630 60 L0 60 Z" fill="var(--green)"/>
    </svg>
    <span class="return-address">Suite 6, 19 Marlowe St, Harwick, NSW 2199</span>
  </div>

</body>
</html>
```